Kestrel Facilities Business Card Design

We would now like to design business cards with the new Kestrel Facilities logo

Target Market(s)

Professional

Industry/Entity Type

Professional services

Contact Information for Business Card

Employee name, title, phone number, email address, corporate office address and logo.

Font styles to use
Sans Serif

Colors
0054AA
0677BA
7BADD7
CADEEF
E8F1F8

Requirements
Must have
• My logo
Should not have
• any other pictures or images besides my logo

```html
<!DOCTYPE html>
<html lang="en">
<head>
<meta charset="utf-8">
<title>Kestrel Facilities Business Card</title>
<link href="https://fonts.googleapis.com/css2?family=Montserrat:wght@400;500;700&display=swap" rel="stylesheet">
<style>
  :root {
    --brand-blue: #0677e6;
    --ink: #333333;
    --ink-dark: #111111;
    --paper: #ffffff;
    --backdrop: #c9c9c9;
  }
  * { box-sizing: border-box; margin: 0; padding: 0; }
  html, body {
    width: 1200px; height: 800px; overflow: hidden;
    background: var(--backdrop);
    font-family: "Montserrat", sans-serif;
  }
  .sheet {
    width: 1200px; height: 800px;
    display: flex; align-items: center; justify-content: center; gap: 40px;
  }
  .card {
    width: 540px; height: 308px;
    box-shadow: 0 10px 28px rgba(0,0,0,0.18);
    position: relative;
  }
  .card--front {
    background: var(--paper);
    display: flex; align-items: center;
    padding: 0 36px 0 44px;
  }
  .card--back {
    background: var(--brand-blue);
    display: flex; align-items: center; justify-content: center;
  }
  .brand {
    display: flex; align-items: center; gap: 12px;
    font-weight: 700; text-transform: uppercase;
    line-height: 1.02; letter-spacing: 1px;
  }
  .brand__mark { width: 26px; height: 26px; flex: none; }
  .card--front .brand { color: var(--brand-blue); font-size: 27px; width: 220px; }
  .card--front .brand__mark { background: var(--brand-blue); }
  .card--back .brand { color: var(--ink-dark); font-size: 36px; }
  .card--back .brand__mark { background: var(--ink-dark); width: 32px; height: 32px; }
  .contact { border-left: 0; padding-left: 6px; }
  .person {
    border-left: 4px solid var(--brand-blue);
    padding-left: 10px; margin-bottom: 14px;
  }
  .person__name {
    color: var(--brand-blue); font-weight: 700; font-size: 18px; letter-spacing: 0.5px;
  }
  .person__title { color: var(--ink); font-size: 12px; margin-top: 2px; }
  .details { list-style: none; }
  .details__item {
    display: flex; align-items: flex-start; gap: 8px;
    color: var(--ink); font-size: 11.5px; line-height: 1.4; margin-bottom: 4px;
  }
  .details__icon { width: 12px; height: 12px; flex: none; margin-top: 2px; }
  .details__icon path, .details__icon circle, .details__icon rect {
    fill: none; stroke: var(--brand-blue); stroke-width: 1.4;
  }
</style>
</head>
<body>
<main class="sheet">
  <section class="card card--front">
    <div class="brand"><span class="brand__mark"></span><span>Kestrel Facilities</span></div>
    <div class="contact">
      <div class="person">
        <p class="person__name">DANIEL HART</p>
        <p class="person__title">President</p>
      </div>
      <ul class="details">
        <li class="details__item">
          <svg class="details__icon" viewBox="0 0 12 12"><path d="M6 11 C3 7.5 2 6 2 4.5 a4 4 0 0 1 8 0 C10 6 9 7.5 6 11z"/><circle cx="6" cy="4.5" r="1.4"/></svg>
          <span>4120 Birchwood Road<br>Juneau, Alaska 99801</span>
        </li>
        <li class="details__item">
          <svg class="details__icon" viewBox="0 0 12 12"><path d="M2 1.5 h2.5 l1 2.5 -1.4 1 a6 6 0 0 0 2.9 2.9 l1 -1.4 2.5 1 v2.5 a1 1 0 0 1 -1 1 A9 9 0 0 1 1 2.5 a1 1 0 0 1 1 -1z"/></svg>
          <span>907-555-0148</span>
        </li>
        <li class="details__item">
          <svg class="details__icon" viewBox="0 0 12 12"><rect x="1" y="2.5" width="10" height="7"/><path d="M1 2.5 L6 6.5 L11 2.5"/></svg>
          <span>info@kestrelfacilities.com</span>
        </li>
        <li class="details__item">
          <svg class="details__icon" viewBox="0 0 12 12"><circle cx="6" cy="6" r="5"/><path d="M1 6 h10 M6 1 c-2.5 3 -2.5 7 0 10 M6 1 c2.5 3 2.5 7 0 10"/></svg>
          <span>kestrelfacilities.com</span>
        </li>
      </ul>
    </div>
  </section>
  <section class="card card--back">
    <div class="brand"><span class="brand__mark"></span><span>Kestrel<br>Facilities</span></div>
  </section>
</main>
</body>
</html>
```